Keystonery Billboard - Financial Services Company (Investments, Tax Planning and Insurance)

Our new office has a billboard directly above the office building. We'd like something eye-catching with a strong Call to Action, with the main part of the billboard being under 7 words if possible. We'd like you to include a way to get ahold of us (either our website keystoneryllc.example or our phone number 302-418-2907. You may also include in small font something to indicate that we've been serving the area since 1980 (the DE area, the tri-state area, the Marlowe Hollow, etc.)

We offer financial planning, tax planning, and insurance, and we help our clients to focus on their goals and happiness by providing everything they need for lifelong wealth under one roof.

Our logos are attached, we use a triangle logo with green and gray. We use the tagline "discover lasting prosperity" but this does not need to be included.

Potential ideas we have seen from other financial companies-
- the concept that the driver spends more time looking at billboards than planning for their retirement
-something along the lines of "everything you need for your finances is in this building right here" planning, investments, taxes, insurance"
-don't spend your time worrying about retirement, let us help you plan for it
-are you working for your money, or is it working for you?
- retirement takes planning, we're here to help
- ready to retire? talk to us
- need investment advice?
- need help investing?
- crossing your fingers isn't a retirement plan. we can help.
- retiring soon? you need help.

Those are just general ideas, please feel free to be creative.

brand colors:
#00b585
#00b185
#000000
#ffffff
#6d6f75
#6d6f75
#6f7074
#021712
#052e24

```html
<!DOCTYPE html>
<html lang="en">
<head>
<meta charset="utf-8">
<title>Keystonery Billboard</title>
<link rel="stylesheet" href="https://fonts.googleapis.com/css2?family=Bebas+Neue&family=Poppins:wght@500;600;700;800&display=swap">
<style>
  :root {
    --brand-green: #00a878;
    --ink: #242424;
    --band-dark: #262626;
    --band-gray: #6d6f75;
    --paper: #ffffff;
    --stage: #dedede;
    --divider: #d9d9d9;
    --photo-warm: #d9c3a8;
    --photo-cool: #8f9bb3;
  }
  html, body {
    margin: 0;
    padding: 0;
    width: 896px;
    height: 1200px;
    overflow: hidden;
    background: var(--stage);
  }
  .billboard {
    position: absolute;
    left: 28px;
    top: 464px;
    width: 840px;
    height: 272px;
    filter: drop-shadow(6px 10px 8px rgba(0,0,0,0.28));
  }
  .billboard svg { display: block; width: 100%; height: 100%; }
  .headline {
    font-family: "Bebas Neue", Impact, sans-serif;
    fill: var(--ink);
  }
  .subhead {
    font-family: "Poppins", Arial, sans-serif;
    font-weight: 800;
    fill: var(--brand-green);
  }
  .brand-name {
    font-family: "Poppins", Arial, sans-serif;
    font-weight: 600;
    fill: var(--brand-green);
  }
  .service {
    font-family: "Poppins", Arial, sans-serif;
    font-weight: 500;
    fill: var(--paper);
  }
  .phone {
    font-family: "Poppins", Arial, sans-serif;
    font-weight: 800;
    fill: var(--paper);
  }
  .since-top {
    font-family: "Poppins", Arial, sans-serif;
    font-weight: 600;
    fill: var(--paper);
  }
  .since-year {
    font-family: "Poppins", Arial, sans-serif;
    font-weight: 700;
    fill: #111111;
  }
  .tick-box { fill: var(--paper); }
  .tick-mark { fill: none; stroke: var(--brand-green); stroke-width: 3.2; stroke-linecap: round; stroke-linejoin: round; }
</style>
</head>
<body>
  <div class="billboard">
    <svg viewBox="0 0 1465 475" xmlns="http://www.w3.org/2000/svg">
      <defs>
        <linearGradient id="photoTone" x1="0" y1="0" x2="1" y2="1">
          <stop offset="0" stop-color="var(--photo-cool)"/>
          <stop offset="0.55" stop-color="var(--photo-warm)"/>
          <stop offset="1" stop-color="#a88a6e"/>
        </linearGradient>
      </defs>

      <rect class="board-base" x="0" y="0" width="1465" height="475" fill="var(--paper)"/>

      <!-- dark service band -->
      <polygon class="service-band" points="0,357 418,357 510,200 1175,200 1010,475 0,475" fill="var(--band-dark)"/>
      <!-- since-1980 strip -->
      <polygon class="since-strip" points="0,367 410,367 350,475 0,475" fill="var(--brand-green)"/>
      <!-- phone strip -->
      <polygon class="phone-strip" points="425,367 1062,367 1000,475 362,475" fill="var(--band-gray)"/>
      <!-- green corner panel -->
      <polygon class="accent-panel" points="1300,0 1465,0 1465,475 1020,475" fill="var(--brand-green)"/>
      <!-- photo area -->
      <polygon class="photo" role="img" aria-label="Photo of a smiling retired couple embracing"
               points="1315,18 1465,18 1465,475 1095,475 1108,195 1200,150" fill="url(#photoTone)"/>

      <!-- headline -->
      <text class="headline" x="55" y="165" font-size="158" textLength="695" lengthAdjust="spacingAndGlyphs">RETIRING SOON?</text>
      <line class="divider" x1="788" y1="50" x2="788" y2="168" stroke="var(--divider)" stroke-width="2"/>

      <!-- brand name -->
      <rect class="brand-square" x="818" y="86" width="36" height="36" fill="var(--brand-green)"/>
      <text class="brand-name" x="872" y="122" font-size="50">Keystonery</text>

      <!-- subhead -->
      <text class="subhead" x="56" y="266" font-size="74">YOU NEED</text>
      <text class="subhead" x="56" y="330" font-size="74">HELP</text>

      <!-- services -->
      <g class="service-list">
        <g transform="translate(505,254)">
          <rect class="tick-box" width="22" height="20" rx="3"/>
          <polyline class="tick-mark" points="5,10 10,15 19,4"/>
        </g>
        <text class="service" x="534" y="273" font-size="23">Financial planning</text>
        <g transform="translate(764,254)">
          <rect class="tick-box" width="22" height="20" rx="3"/>
          <polyline class="tick-mark" points="5,10 10,15 19,4"/>
        </g>
        <text class="service" x="793" y="273" font-size="23">Investment management</text>
        <g transform="translate(505,293)">
          <rect class="tick-box" width="22" height="20" rx="3"/>
          <polyline class="tick-mark" points="5,10 10,15 19,4"/>
        </g>
        <text class="service" x="534" y="312" font-size="23">Tax planning</text>
        <g transform="translate(764,293)">
          <rect class="tick-box" width="22" height="20" rx="3"/>
          <polyline class="tick-mark" points="5,10 10,15 19,4"/>
        </g>
        <text class="service" x="793" y="312" font-size="23">Insurance</text>
      </g>

      <!-- since -->
      <text class="since-top" x="58" y="410" font-size="27">SERVING THIS AREA</text>
      <text class="since-year" x="58" y="442" font-size="27">SINCE 1980</text>

      <!-- phone -->
      <text class="phone" x="445" y="448" font-size="74" textLength="555" lengthAdjust="spacingAndGlyphs">302-418-2907</text>
    </svg>
  </div>
</body>
</html>
```